Rig up a website for a Rigging Company

We already have a logo. Looking for a website design that works on pavlune.com.
Our rigging company uses semi trucks, forklifts, and similar equipment to move large machines.
Our logo is white, black and red.

Target Market(s)

Medical Industry (moving medical equipment), Utility Industry (power equipment), Food Industry (moving bottling/packing equipment), US Government (large equipment)

Industry/Entity Type

It Company

Coding

Coded - Design and coding required

Number of Pages Required

5+ page

Font styles to use
Sans Serif

Colors
ec1f27
ffffff
0355a3

Requirements
Must have
• Home page, About page, Services Page, and Contact Information page
Nice to have
• Pictures of semi and forklifts and ability to insert our own pictures of our equipment

```html
<!DOCTYPE html>
<html lang="en">
<head>
<meta charset="utf-8">
<title>Halvern Rigging — Home</title>
<link href="https://fonts.googleapis.com/css2?family=Montserrat:wght@300;400;500;600;700&display=swap" rel="stylesheet">
<style>
  :root {
    --red: #ec2f3c;
    --red-dark: #d92431;
    --ink: #111111;
    --text-soft: #7a7a7a;
    --white: #ffffff;
    --shadow: #dcdcdc;
    --footer-bg: #f7f7f7;
  }
  * { margin: 0; padding: 0; box-sizing: border-box; }
  html, body { width: 1200px; height: 2302px; overflow: hidden; }
  body {
    position: relative;
    background: var(--white);
    font-family: "Montserrat", Arial, sans-serif;
    color: var(--ink);
  }
  .abs { position: absolute; }

  /* Header */
  .site-header { left: 0; top: 0; width: 1200px; height: 80px; background: var(--white); }
  .brand {
    position: absolute; left: 246px; top: 26px;
    display: flex; align-items: center; gap: 8px;
    font-weight: 700; font-size: 21px; color: var(--ink); letter-spacing: -0.3px;
  }
  .brand-mark { width: 12px; height: 12px; background: var(--red); }
  .main-nav a {
    position: absolute; top: 40px;
    font-size: 10.5px; font-weight: 700; color: var(--ink);
    text-decoration: none; letter-spacing: 0.3px;
  }
  .main-nav a.is-active { color: var(--red); }

  /* Hero */
  .hero {
    left: 0; top: 80px; width: 1200px; height: 388px;
    background: linear-gradient(180deg, #3e5f8f 0%, #6b86a8 35%, #a7a0a0 58%, #d28a4a 66%, #5f6670 72%, #7d8794 100%);
  }
  .hero-title {
    right: 247px; top: 211px; font-size: 20px; font-weight: 500;
    color: var(--white); letter-spacing: 0.4px; text-align: right;
  }
  .hero-lead {
    right: 247px; top: 250px; width: 380px; text-align: right;
    font-size: 15px; font-weight: 300; line-height: 20.5px; color: var(--white);
  }
  .btn-more {
    left: 843px; top: 331px; width: 110px; height: 31px;
    background: var(--red); color: var(--white);
    font-size: 9.5px; font-weight: 700; letter-spacing: 0.3px;
    display: flex; align-items: center; justify-content: center;
  }
  .hero-dots span {
    position: absolute; left: 20px; width: 7px; height: 7px; border-radius: 50%;
    background: var(--white);
  }
  .hero-dots span.is-current { background: var(--red); }

  /* Our rigging */
  .section-title { font-size: 24px; font-weight: 700; color: var(--ink); letter-spacing: 0.3px; }
  .rig-band { background: var(--red); }
  .rig-photo { }
  .rig-shadow { background: var(--shadow); }
  .rig-name { font-size: 21px; font-weight: 600; color: var(--white); }
  .rig-text {
    font-size: 10.3px; line-height: 20px; color: var(--white); font-weight: 400;
  }

  /* News */
  .news-date {
    width: 101px; height: 99px; background: var(--red); color: var(--white);
    font-size: 21px; font-weight: 600; line-height: 20px; text-align: center;
    display: flex; flex-direction: column; justify-content: center;
  }
  .news-head { width: 240px; font-size: 14.5px; line-height: 20.5px; color: var(--text-soft); }
  .news-body { width: 235px; font-size: 10.2px; line-height: 20px; color: var(--text-soft); }

  /* Footer */
  .site-footer { left: 0; top: 2198px; width: 1200px; height: 104px; background: var(--footer-bg); }
  .site-footer .brand { top: 42px; }
  .copyright {
    position: absolute; left: 720px; top: 49px;
    font-size: 9.5px; font-weight: 700; color: var(--ink); letter-spacing: 0.2px;
  }
</style>
</head>
<body>

<header class="site-header abs">
  <div class="brand"><span class="brand-mark"></span>Halvern Rigging</div>
  <nav class="main-nav">
    <a class="is-active" href="#" style="left:599px">HOME</a>
    <a href="#" style="left:663px">ABOUT US</a>
    <a href="#" style="left:748px">SERVICES</a>
    <a href="#" style="left:829px">FAQ'S</a>
    <a href="#" style="left:893px">CONTACT US</a>
  </nav>
</header>

<section class="hero abs" role="img" aria-label="Offshore rig and cranes at a harbour under a sunset sky"></section>
<div class="hero-dots">
  <span class="is-current" style="top:290px"></span>
  <span style="top:308px"></span>
  <span style="top:325px"></span>
  <span style="top:342px"></span>
</div>
<h1 class="hero-title abs">WE ARE A RIGGING COMPANY</h1>
<p class="hero-lead abs">Sed ut perspiciatis unde omnis iste natus error sit voluptatem accusantium doloremque laudantium, totam rem aperiam, eaque ipsa</p>
<a class="btn-more abs">READ MORE</a>

<h2 class="section-title abs" style="left:238px;top:580px">OUR RIGGING</h2>

<!-- Semi trucks -->
<div class="rig-band abs" style="left:0;top:643px;width:630px;height:209px;clip-path:polygon(0 0,574px 0,630px 100%,0 100%)"></div>
<div class="rig-shadow abs" style="left:590px;top:623px;width:610px;height:272px;clip-path:polygon(0 0,100% 0,100% 100%,42px 100%)"></div>
<div class="rig-photo abs" role="img" aria-label="Red semi truck parked on a gravel lot" style="left:580px;top:611px;width:620px;height:273px;background:linear-gradient(135deg,#9eb4cf 0%,#c9c3b9 40%,#b3232b 55%,#6f6a66 100%);clip-path:polygon(0 0,100% 0,100% 100%,42px 100%)"></div>
<h3 class="rig-name abs" style="left:244px;top:682px">Semi Trucks</h3>
<p class="rig-text abs" style="left:244px;top:724px;width:345px">At vero eos et accusamus et iusto odio dignissimos ducimus qui blanditiis praesentium voluptatum deleniti atque corrupti quos dolores et quas molestias excepturi sint occaecati cupiditate non provident, similique sunt in culpa qui officia deserunt mollitia animi</p>

<!-- Forklifts -->
<div class="rig-shadow abs" style="left:0;top:976px;width:630px;height:270px;clip-path:polygon(0 0,100% 0,46px 100%,0 100%)"></div>
<div class="rig-shadow abs" style="left:0;top:976px;width:580px;height:270px"></div>
<div class="rig-photo abs" role="img" aria-label="Yellow forklift in a warehouse aisle" style="left:0;top:964px;width:622px;height:273px;background:linear-gradient(135deg,#c7ccd4 0%,#e3e4e6 40%,#d9a23a 62%,#8e8f93 100%);clip-path:polygon(0 0,100% 0,576px 100%,0 100%)"></div>
<div class="rig-band abs" style="left:571px;top:995px;width:629px;height:208px;clip-path:polygon(51px 0,100% 0,100% 100%,0 100%)"></div>
<h3 class="rig-name abs" style="left:672px;top:1035px">Forklifts</h3>
<p class="rig-text abs" style="left:672px;top:1078px;width:345px">At vero eos et accusamus et iusto odio dignissimos ducimus qui blanditiis praesentium voluptatum deleniti atque corrupti quos dolores et quas molestias excepturi sint occaecati cupiditate non provident, similique sunt in culpa qui officia deserunt mollitia animi</p>

<!-- Large machines -->
<div class="rig-band abs" style="left:0;top:1366px;width:630px;height:207px;clip-path:polygon(0 0,574px 0,630px 100%,0 100%)"></div>
<div class="rig-shadow abs" style="left:590px;top:1344px;width:610px;height:272px;clip-path:polygon(0 0,100% 0,100% 100%,42px 100%)"></div>
<div class="rig-photo abs" role="img" aria-label="Yellow excavator and dump truck at a quarry" style="left:580px;top:1332px;width:620px;height:273px;background:linear-gradient(135deg,#3f7fcf 0%,#8fb5e0 35%,#d8ab2a 55%,#4d4638 100%);clip-path:polygon(0 0,100% 0,100% 100%,42px 100%)"></div>
<h3 class="rig-name abs" style="left:244px;top:1402px">Large Machines</h3>
<p class="rig-text abs" style="left:244px;top:1445px;width:345px">At vero eos et accusamus et iusto odio dignissimos ducimus qui blanditiis praesentium voluptatum deleniti atque corrupti quos dolores et quas molestias excepturi sint occaecati cupiditate non provident, similique sunt in culpa qui officia deserunt mollitia animi</p>

<!-- Latest news -->
<h2 class="section-title abs" style="left:0;width:1200px;text-align:center;top:1699px">LATEST NEWS</h2>

<div class="news-date abs" style="left:246px;top:1794px">MAR<br>23<br>2017</div>
<h4 class="news-head abs" style="left:373px;top:1789px;font-weight:400">Presentium voluptatum deleniti atque corrupti quos dolores</h4>
<p class="news-body abs" style="left:373px;top:1849px">At vero eos et accusamus et iusto odio dignissimos ducimus qui blanditiis praesentium voluptatum deleniti atque corrupti quos dolores et quas molestias excepturi sint occaecati</p>

<div class="news-date abs" style="left:611px;top:1794px">MAR<br>23<br>2017</div>
<h4 class="news-head abs" style="left:738px;top:1789px;font-weight:400">Presentium voluptatum deleniti atque corrupti quos dolores</h4>
<p class="news-body abs" style="left:738px;top:1849px">At vero eos et accusamus et iusto odio dignissimos ducimus qui blanditiis praesentium voluptatum deleniti atque corrupti quos dolores et quas molestias excepturi sint occaecati</p>

<div class="news-date abs" style="left:246px;top:1992px">MAR<br>23<br>2017</div>
<h4 class="news-head abs" style="left:373px;top:1988px;font-weight:400">Presentium voluptatum deleniti atque corrupti quos dolores</h4>
<p class="news-body abs" style="left:373px;top:2048px">At vero eos et accusamus et iusto odio dignissimos ducimus qui blanditiis praesentium voluptatum deleniti atque corrupti quos dolores et quas molestias excepturi sint occaecati</p>

<div class="news-date abs" style="left:611px;top:1992px">MAR<br>23<br>2017</div>
<h4 class="news-head abs" style="left:738px;top:1988px;font-weight:400">Presentium voluptatum deleniti atque corrupti quos dolores</h4>
<p class="news-body abs" style="left:738px;top:2048px">At vero eos et accusamus et iusto odio dignissimos ducimus qui blanditiis praesentium voluptatum deleniti atque corrupti quos dolores et quas molestias excepturi sint occaecati</p>

<footer class="site-footer abs">
  <div class="brand"><span class="brand-mark"></span>Halvern Rigging</div>
  <p class="copyright">© 2017 COMPANY NAME &nbsp;| ALL RIGHTS RESERVED</p>
</footer>

</body>
</html>
```